Website Design for a holiday home letting busines

We require a redesign of our present website www.pinebrookstays.com. We want the website to stand out and look professional and clean to make holiday hunters want to book a caravan or lodge holiday with us. Our logo is red however we DO NOT want the website to be red. We want a natural colour scheme.

The final design should communicate that we are a professional company to book with.

On the home page we require;
Overview of company
Photo
Search box for holiday (check in)
Late Deals
Reviews
News

We would like the following pages designed; home page, available dates page, caravans page, content page.

The website should be responsive for smart phones. One website I do like is http://www.verdoliso.be/nl/

Target Market(s)

Families

Industry/Entity Type

Travel

Number of Pages Required

5+ page

Font styles to use
Serif

Requirements
Must have
• The project must be responsive for mobile phones and tablets.
• Ability to search for holiday home holidays
• We want a natural colour scheme.
Nice to have
• A style we like is http://www.verdoliso.be/nl/
Should not have
• Do not use red as a colour for the website. Our logo is red so this is the only time we want this used.

```html
<!DOCTYPE html>
<html lang="en">
<head>
<meta charset="utf-8">
<title>Pinebrook Stays – Holiday Lodges and Caravans</title>
<link rel="stylesheet" href="https://fonts.googleapis.com/css2?family=Open+Sans:wght@400;600;700;800&display=swap">
<style>
:root{
  --ink:#2b2826;
  --dark:#3a3632;
  --darker:#24211f;
  --nav:#45413c;
  --orange:#e8711f;
  --orange-deep:#c95d12;
  --cream:#efece7;
  --paper:#ffffff;
  --muted:#a7a19a;
  --text:#5d5852;
  --brand:#d2232a;
}
*{box-sizing:border-box;margin:0;padding:0}
html,body{width:1200px;height:2548px;overflow:hidden}
body{font-family:"Open Sans",Arial,sans-serif;color:var(--text);background:var(--cream);font-size:12px;line-height:1.6}
.wrap{width:976px;margin:0 auto;position:relative}
.photo{display:block}
h2.section-title{font-size:20px;font-weight:600;letter-spacing:.5px;text-transform:uppercase;color:var(--ink)}
h2.section-title::after{content:"";display:block;width:40px;height:3px;background:var(--orange);margin-top:8px}

/* header */
.site-header{height:68px;background:var(--paper)}
.site-header .wrap{display:flex;align-items:center;justify-content:space-between;height:68px}
.brand{display:flex;align-items:center;gap:10px}
.brand-dot{width:40px;height:40px;border-radius:50%;background:var(--brand)}
.brand-name{font-size:22px;font-weight:700;color:var(--ink);line-height:1.1}
.brand-sub{font-size:10px;color:var(--muted)}
.header-actions{display:flex;align-items:center;gap:16px}
.phone{display:flex;align-items:center;gap:6px;font-weight:600;color:var(--ink);font-size:13px}
.btn-book{background:var(--orange);color:#fff;font-weight:700;font-size:11px;padding:8px 16px;letter-spacing:.5px}

/* nav */
.main-nav{height:32px;background:var(--nav)}
.main-nav ul{list-style:none;display:flex;height:32px}
.main-nav li{color:#ddd8d2;font-size:10px;font-weight:600;letter-spacing:.5px;padding:0 19px;line-height:32px;border-right:1px solid #55504a}
.main-nav li.active{background:var(--darker);color:#fff}

/* hero */
.hero{height:620px;position:relative;background:linear-gradient(160deg,#7fa9c4 0%,#c9b39a 45%,#9f7550 75%,#5f4a3a 100%)}
.hero-caption{position:absolute;left:190px;top:420px;background:rgba(43,40,38,.78);color:#fff;font-size:22px;font-weight:600;padding:14px 28px;letter-spacing:1px}
.hero-dots{position:absolute;left:0;right:0;bottom:22px;display:flex;justify-content:center;gap:8px}
.hero-dots span{width:10px;height:10px;border-radius:50%;background:rgba(255,255,255,.5)}
.hero-dots span.on{background:var(--orange)}

/* availability */
.availability{height:140px;display:flex;background:var(--orange)}
.availability-title{width:370px;background:var(--darker);color:#fff;font-size:22px;font-weight:700;line-height:1.15;padding:44px 0 0 112px;text-transform:uppercase}
.availability-form{flex:1;display:flex;align-items:flex-end;gap:14px;padding:0 0 50px 30px}
.field label{display:block;color:#fff;font-size:10px;margin-bottom:4px}
.field .input{background:#fff;height:30px;width:140px;border:1px solid var(--orange-deep)}
.field.small .input{width:78px}
.btn-check{background:var(--darker);color:#fff;font-size:11px;font-weight:700;height:30px;padding:0 22px;line-height:30px;margin-left:10px}

/* welcome */
.welcome{height:340px;background:var(--dark);padding-top:40px}
.welcome .wrap{display:flex;gap:40px}
.welcome-text{flex:1}
.welcome-text h2{color:#fff;font-size:20px;font-weight:600;text-transform:uppercase}
.welcome-text h3{color:var(--orange);font-size:13px;font-weight:700;text-transform:uppercase;margin:4px 0 12px}
.welcome-text p{color:#bdb6ae;font-size:11px;margin-bottom:10px}
.gallery{width:300px}
.gallery h2{color:#fff;font-size:16px;font-weight:600;text-transform:uppercase;margin-bottom:12px}
.gallery .photo{height:180px;border:3px solid #fff;background:linear-gradient(135deg,#b7c77a,#e8e3c9 60%,#9bb05a)}

/* card rows */
.card-row{display:flex;gap:18px;margin-top:24px}
.card{width:230px}
.card .photo{height:140px;position:relative}
.card .cap{font-size:11px;margin-top:8px}
.card .overlay{position:absolute;left:50%;top:50%;transform:translate(-50%,-50%);background:var(--orange);color:#fff;font-size:10px;font-weight:700;padding:6px 14px}
.caravans{height:300px;padding-top:40px;background:var(--cream)}
.caravans .cap{color:var(--ink)}
.deals{height:300px;padding-top:40px;background:var(--dark)}
.deals h2.section-title{color:#fff}
.deals .cap{color:#e7e1da}
.p1{background:linear-gradient(160deg,#d9d4cc,#a49888)}
.p2{background:linear-gradient(160deg,#e6e1d8,#8c7d6c)}
.p3{background:linear-gradient(160deg,#6a4e3a,#c9a27c)}
.p4{background:linear-gradient(160deg,#ece6dc,#b3765a)}
.p5{background:linear-gradient(180deg,#8eb6d6,#d7dde2 60%,#5f6a70)}
.p6{background:linear-gradient(180deg,#e7c79b,#b58a5c 60%,#4f3b2b)}
.p7{background:linear-gradient(180deg,#c2d98a,#e9e6d0 60%,#7c6a55)}
.p8{background:linear-gradient(180deg,#6e8fb8,#d9c9b0 60%,#3e3a36)}

/* three columns */
.columns{height:380px;padding-top:36px;background:var(--cream)}
.columns .wrap{display:flex;gap:38px}
.col{width:300px}
.col h2.section-title{font-size:16px;margin-bottom:16px}
.item{display:flex;gap:10px;margin-bottom:14px}
.thumb{width:70px;height:48px;flex:none}
.item-title{color:var(--orange);font-weight:600;font-size:11px}
.item p{font-size:10px;line-height:1.45}
.stars{color:var(--orange);font-size:10px;letter-spacing:1px}
.date{color:var(--orange);font-weight:700;font-size:11px}
.datebox{width:32px;height:32px;background:var(--orange);flex:none}
.feed{background:#fff;border:1px solid #ddd7cf;padding:12px}
.feed .item:last-child{margin-bottom:0}

/* newsletter */
.newsletter{height:80px;background:var(--cream);position:relative}
.newsletter::before{content:"";position:absolute;left:0;right:0;top:38px;height:4px;background:var(--orange)}
.btn-news{position:absolute;left:50%;top:22px;transform:translateX(-50%);background:var(--darker);color:#fff;font-size:11px;font-weight:700;letter-spacing:.5px;padding:0 30px;height:36px;line-height:36px;display:flex;align-items:center;gap:10px}

/* footer */
.site-footer{height:260px;background:var(--darker);padding-top:36px;color:#a49d95}
.site-footer .wrap{display:flex;gap:34px}
.fcol{width:150px;font-size:10px;line-height:2}
.fcol.contact{width:190px}
.fcol h4{color:#fff;font-size:12px;font-weight:700;text-transform:uppercase;margin-bottom:8px}
.fline{display:flex;align-items:center;gap:6px}
.badge-col{flex:1;display:flex;flex-direction:column;align-items:flex-end}
.badge{width:80px;height:80px;border-radius:50%;background:#6f9a4a;border:4px solid #e8e3dc}
.pay-label{color:#fff;font-size:11px;font-weight:700;margin:18px 0 6px}
.cards{display:flex;gap:6px}
.cards span{width:34px;height:22px;background:#e8e3dc;border-radius:2px}
.copyright{height:28px;background:#1a1816;color:#7f786f;font-size:10px;line-height:28px}
</style>
</head>
<body>

<header class="site-header">
  <div class="wrap">
    <div class="brand">
      <span class="brand-dot"></span>
      <div>
        <div class="brand-name">Pinebrook Stays</div>
        <div class="brand-sub">at Fernhollow Holiday Park</div>
      </div>
    </div>
    <div class="header-actions">
      <div class="phone">
        <svg width="14" height="14" viewBox="0 0 24 24"><path fill="#e8711f" d="M6.6 10.8a15 15 0 006.6 6.6l2.2-2.2c.3-.3.7-.4 1-.2 1.1.4 2.3.6 3.6.6.6 0 1 .4 1 1V20c0 .6-.4 1-1 1A17 17 0 013 4c0-.6.4-1 1-1h3.5c.6 0 1 .4 1 1 0 1.3.2 2.5.6 3.6.1.3 0 .7-.2 1z"/></svg>
        01632 960 418
      </div>
      <div class="btn-book">BOOK NOW</div>
    </div>
  </div>
</header>

<nav class="main-nav">
  <div class="wrap">
    <ul>
      <li class="active">HOME</li>
      <li>NEWS</li>
      <li>BROCHURE</li>
      <li>CARAVANS &amp; LODGES</li>
      <li>PAYMENT TERMS</li>
      <li>FREQUENT QUESTIONS</li>
      <li>LOCAL ATTRACTIONS</li>
      <li>CONTACT US</li>
    </ul>
  </div>
</nav>

<section class="hero photo" role="img" aria-label="Photo of a smiling family group taking a selfie on a sunny beach">
  <div class="hero-caption">PRIVATE HOLIDAY RENTALS</div>
  <div class="hero-dots"><span></span><span class="on"></span><span></span><span></span></div>
</section>

<section class="availability">
  <div class="availability-title">Check<br>Availability</div>
  <div class="availability-form">
    <div class="field"><label>Arrival date</label><div class="input"></div></div>
    <div class="field"><label>Departure date</label><div class="input"></div></div>
    <div class="field small"><label>Adults</label><div class="input"></div></div>
    <div class="field small"><label>Children</label><div class="input"></div></div>
    <div class="btn-check">CHECK NOW</div>
  </div>
</section>

<section class="welcome">
  <div class="wrap">
    <div class="welcome-text">
      <h2>Welcome to Pinebrook Stays</h2>
      <h3>No deposit holidays</h3>
      <p>Book your stay with us and pay nothing up front. Our lodges and caravans sit in a quiet corner of Fernhollow Holiday Park, a short walk from the beach, the pool and the play areas. Every home is cleaned, checked and ready for your family the moment you arrive.</p>
      <p>We are a small, family run letting business and we know every one of our homes well. Tell us what you need and we will help you find the right fit for your group and your budget.</p>
      <p>Pick your dates, choose your home and pay the balance four weeks before you arrive. It really is that simple, and our team is on hand seven days a week to answer any questions.</p>
    </div>
    <aside class="gallery">
      <h2>Our Gallery</h2>
      <div class="photo" role="img" aria-label="Photo of children relaxing on a lawn in the sunshine"></div>
    </aside>
  </div>
</section>

<section class="caravans">
  <div class="wrap">
    <h2 class="section-title">Our Caravans and Lodges</h2>
    <div class="card-row">
      <div class="card"><div class="photo p1" role="img" aria-label="Photo of a bright caravan lounge"></div><div class="cap">The Larchmere</div></div>
      <div class="card"><div class="photo p2" role="img" aria-label="Photo of a lodge living room with sofa"></div><div class="cap">The Hazelwood</div></div>
      <div class="card"><div class="photo p3" role="img" aria-label="Photo of a warm lodge interior with dining area"><span class="overlay">BOOK NOW</span></div><div class="cap">The Rowan</div></div>
      <div class="card"><div class="photo p4" role="img" aria-label="Photo of a caravan sitting room"></div><div class="cap">The Bramble</div></div>
    </div>
  </div>
</section>

<section class="deals">
  <div class="wrap">
    <h2 class="section-title">Late Deals</h2>
    <div class="card-row">
      <div class="card"><div class="photo p5" role="img" aria-label="Photo of a lodge exterior with decking"></div><div class="cap">The Hazelwood</div></div>
      <div class="card"><div class="photo p6" role="img" aria-label="Photo of a lodge lit up at dusk"></div><div class="cap">The Bramble</div></div>
      <div class="card"><div class="photo p7" role="img" aria-label="Photo of a caravan lounge with green accents"></div><div class="cap">The Larchmere</div></div>
      <div class="card"><div class="photo p8" role="img" aria-label="Photo of a holiday home beside a pool"></div><div class="cap">The Meadowlark</div></div>
    </div>
  </div>
</section>

<section class="columns">
  <div class="wrap">
    <div class="col">
      <h2 class="section-title">Latest Reviews</h2>
      <div class="item"><div class="thumb p5" role="img" aria-label="Photo of a lodge"></div><div><div class="item-title">The Alderley – a 5 star stay</div><div class="stars">★★★★★</div><p>Spotless home and lovely staff.</p></div></div>
      <div class="item"><div class="thumb p2" role="img" aria-label="Photo of a lounge"></div><div><div class="item-title">Lovely quiet spot</div><div class="stars">★★★★★</div><p>We will be back next summer.</p></div></div>
      <div class="item"><div class="thumb p6" role="img" aria-label="Photo of a lodge at dusk"></div><div><div class="item-title">Kids adored the pool</div><div class="stars">★★★★☆</div><p>Great value for a family week.</p></div></div>
      <div class="item"><div class="thumb p1" role="img" aria-label="Photo of a caravan interior"></div><div><div class="item-title">Perfect short break</div><div class="stars">★★★★★</div><p>Easy booking from start to end.</p></div></div>
    </div>
    <div class="col">
      <h2 class="section-title">News from our Blog</h2>
      <div class="item"><div class="datebox"></div><div><div class="date">Aug 12, 2015</div><p>New lodges arrive on the park just in time for autumn breaks.</p></div></div>
      <div class="item"><div class="datebox"></div><div><div class="date">Aug 09, 2015</div><p>Five family days out within half an hour of the park.</p></div></div>
      <div class="item"><div class="datebox"></div><div><div class="date">Aug 03, 2015</div><p>Our late deals for the school holidays are now live.</p></div></div>
      <div class="item"><div class="datebox"></div><div><div class="date">Jul 28, 2015</div><p>What to pack for a week in a lodge by the sea.</p></div></div>
    </div>
    <div class="col">
      <h2 class="section-title">Community Feed</h2>
      <div class="feed">
        <div class="item"><div class="thumb p7" role="img" aria-label="Photo of guests on a lawn"></div><p>Sunny start to the week on the park, thanks for all the photos!</p></div>
        <div class="item"><div class="thumb p3" role="img" aria-label="Photo of a lodge interior"></div><p>The Rowan has had a fresh new look inside this spring.</p></div>
        <div class="item"><div class="thumb p8" role="img" aria-label="Photo of a pool area"></div><p>Only two weeks left of our summer offers, book soon.</p></div>
        <div class="item"><div class="thumb p4" role="img" aria-label="Photo of a caravan lounge"></div><p>Thank you to all our guests for the kind words.</p></div>
      </div>
    </div>
  </div>
</section>

<section class="newsletter">
  <div class="btn-news">
    <svg width="14" height="10" viewBox="0 0 14 10"><rect x=".5" y=".5" width="13" height="9" fill="none" stroke="#e8711f"/><path d="M.5.5L7 6 13.5.5" fill="none" stroke="#e8711f"/></svg>
    SUBSCRIBE TO OUR NEWSLETTER
  </div>
</section>

<footer class="site-footer">
  <div class="wrap">
    <div class="fcol contact">
      <h4>Contact Us</h4>
      <div class="fline"><svg width="10" height="12" viewBox="0 0 10 14"><path fill="#e8711f" d="M5 0a5 5 0 00-5 5c0 4 5 9 5 9s5-5 5-9a5 5 0 00-5-5zm0 7a2 2 0 110-4 2 2 0 010 4z"/></svg>Pinebrook Stays, Fernhollow Park</div>
      <div class="fline" style="padding-left:16px">Shore Lane, Northfield NF2 4QT</div>
      <div class="fline"><svg width="10" height="10" viewBox="0 0 24 24"><path fill="#e8711f" d="M6.6 10.8a15 15 0 006.6 6.6l2.2-2.2c.3-.3.7-.4 1-.2 1.1.4 2.3.6 3.6.6.6 0 1 .4 1 1V20c0 .6-.4 1-1 1A17 17 0 013 4c0-.6.4-1 1-1h3.5c.6 0 1 .4 1 1 0 1.3.2 2.5.6 3.6.1.3 0 .7-.2 1z"/></svg>01632 960 418</div>
      <div class="fline"><svg width="10" height="8" viewBox="0 0 14 10"><rect x=".5" y=".5" width="13" height="9" fill="none" stroke="#e8711f"/><path d="M.5.5L7 6 13.5.5" fill="none" stroke="#e8711f"/></svg>www.pinebrookstays.com</div>
    </div>
    <div class="fcol">
      <h4>Information</h4>
      <div>About Us</div><div>Brochure</div><div>Payment Terms</div><div>Privacy Policy</div><div>Site Map</div>
    </div>
    <div class="fcol">
      <h4>Why Choose Us</h4>
      <div>No deposit holidays</div><div>Family run business</div><div>Homes checked weekly</div><div>Friendly local team</div><div>Best price promise</div>
    </div>
    <div class="fcol">
      <h4>Quick Links</h4>
      <div>Caravans &amp; Lodges</div><div>Available Dates</div><div>Late Deals</div><div>Our Blog</div><div>Contact Us</div>
    </div>
    <div class="badge-col">
      <div class="badge"></div>
      <div class="pay-label">PAYMENT</div>
      <div class="cards"><span></span><span></span><span></span><span></span></div>
    </div>
  </div>
</footer>
<div class="copyright"><div class="wrap">Copyright © 2015 Pinebrook Stays. All Rights Reserved.</div></div>

</body>
</html>
```